Roofing Contractor business card redesign

I want to redesign my business card with a fresh, eye catching concept

Target Market(s)

Residential Roofing Clients, potential employees, and subcontractors.

Industry/Entity Type

Business

Colors

Designer to choose colors to be used in the design.

Requirements
Nice to have
• I just want something that's more pleasing to the eye. You can use a combination of either / or of my logos.

```html
<!DOCTYPE html>
<html lang="en">
<head>
<meta charset="utf-8">
<title>Bright Crew – Business Card</title>
<link rel="stylesheet" href="https://fonts.googleapis.com/css2?family=Oswald:wght@500;700&family=Work+Sans:wght@400&family=Open+Sans:wght@700&display=swap">
<style>
  :root {
    --bg: #2b2b2b;
    --brown: #46120e;
    --orange: #f3852a;
    --white: #ffffff;
    --ink: #2f2522;
    --rule: #c9a27e;
  }
  * { margin: 0; padding: 0; box-sizing: border-box; }
  html, body { width: 1200px; height: 930px; overflow: hidden; background: var(--bg); }
  .canvas { position: relative; width: 1200px; height: 930px; }

  .card {
    position: absolute; left: 278px; width: 644px; height: 368px;
    border-radius: 20px; overflow: hidden;
  }
  .card--front { top: 76px; background: var(--white); }
  .card--back  { top: 486px; background: var(--orange); }

  .front-wave { position: absolute; inset: 0; width: 644px; height: 368px; }

  .front-brand {
    position: absolute; left: 35px; top: 58px; width: 150px; height: 178px;
    display: flex; flex-direction: column; align-items: center; gap: 12px;
  }
  .front-brand__dot { width: 110px; height: 110px; border-radius: 50%; background: var(--brown); }
  .front-brand__name {
    font-family: "Oswald", sans-serif; font-weight: 700; font-size: 30px;
    color: var(--brown); line-height: 1; white-space: nowrap;
  }

  .holder { position: absolute; right: 36px; top: 172px; text-align: right; }
  .holder__name {
    font-family: "Oswald", sans-serif; font-weight: 500; font-size: 29px;
    letter-spacing: 1px; color: var(--orange); line-height: 36px;
  }
  .holder__title {
    font-family: "Work Sans", sans-serif; font-size: 16.5px; color: var(--ink); line-height: 20px;
  }

  .divider { position: absolute; left: 35px; right: 35px; top: 264px; height: 1px; background: var(--rule); }

  .address, .contacts {
    position: absolute; font-family: "Work Sans", sans-serif; font-size: 16px;
    color: var(--ink); line-height: 20px;
  }
  .address { left: 35px; top: 298px; }
  .contacts { right: 36px; top: 278px; text-align: right; }
  .contacts li { list-style: none; display: flex; justify-content: flex-end; align-items: center; gap: 12px; }
  .contacts svg { width: 12px; height: 12px; flex: none; }

  .back-brand {
    position: absolute; left: 0; right: 0; top: 120px;
    display: flex; flex-direction: column; align-items: center;
  }
  .back-brand__row { display: flex; align-items: center; gap: 12px; }
  .back-brand__word {
    font-family: "Oswald", sans-serif; font-weight: 700; font-size: 70px;
    color: var(--brown); line-height: 1;
  }
  .back-brand__dot { width: 92px; height: 92px; border-radius: 50%; background: var(--brown); }
  .back-brand__tag {
    margin-top: 10px; font-family: "Open Sans", sans-serif; font-weight: 700;
    font-size: 27px; color: var(--brown);
  }
</style>
</head>
<body>
<main class="canvas">
  <section class="card card--front">
    <svg class="front-wave" viewBox="0 0 644 368" aria-hidden="true">
      <path fill="var(--orange)" d="M0 50 C150 5 280 20 400 95 C480 140 590 130 644 116 V0 H0 Z"/>
      <path fill="var(--brown)" d="M0 42 C150 -5 300 20 410 80 C490 120 590 110 644 92 V0 H0 Z"/>
    </svg>

    <div class="front-brand">
      <span class="front-brand__dot"></span>
      <span class="front-brand__name">Bright Crew</span>
    </div>

    <div class="holder">
      <h1 class="holder__name">SAM HOLLOWAY</h1>
      <p class="holder__title">Marlow Certified Roof Inspector</p>
      <p class="holder__title">Licensed Property Adjuster</p>
    </div>

    <div class="divider"></div>

    <address class="address" style="font-style:normal">
      4410 Cedar Bend Road<br>
      Suite 118 Plano, TX 75093
    </address>

    <ul class="contacts">
      <li>(555) 214-3800
        <svg viewBox="0 0 12 12"><path fill="var(--orange)" d="M2.5 1 L4.5 1 L5.2 3.6 L4 4.6 C4.7 6 6 7.3 7.4 8 L8.4 6.8 L11 7.5 L11 9.5 C11 10.3 10.3 11 9.5 11 C5 11 1 7 1 2.5 C1 1.7 1.7 1 2.5 1 Z"/></svg>
      </li>
      <li>(555) 367-9021
        <svg viewBox="0 0 12 12"><rect x="3" y="0.8" width="6.4" height="10.4" rx="1.2" fill="none" stroke="var(--orange)" stroke-width="1.4"/><circle cx="6.2" cy="9.2" r="0.7" fill="var(--orange)"/></svg>
      </li>
      <li>sam@brightcrewtx.com
        <svg viewBox="0 0 12 12"><rect x="0.8" y="2.5" width="10.4" height="7" rx="0.8" fill="none" stroke="var(--orange)" stroke-width="1.2"/><path d="M1 3 L6 6.6 L11 3" fill="none" stroke="var(--orange)" stroke-width="1.2"/></svg>
      </li>
    </ul>
  </section>

  <section class="card card--back">
    <div class="back-brand">
      <div class="back-brand__row">
        <span class="back-brand__word">Bright</span>
        <span class="back-brand__dot"></span>
        <span class="back-brand__word">Crew</span>
      </div>
      <p class="back-brand__tag">General Contractors, Inc.</p>
    </div>
  </section>
</main>
</body>
</html>
```